Diverse, up-scale salon needs eye-catching, unique business cards.

We are looking for a unique business card design for our stylist but that can also be multi functional and used for appointment reminder and referrals. I will need a design in a format that I can modify names and titles going forward. In the past we have had a dark background with the logo on one side, and stylist and contact information on the other but we are open to all ideas. I have included our mission statement as well as branded colors below. The statement doesn't need to go on the card, it's just a reference for target market. We need space for the stylists name, title, instagram handle and then the salons phone number, website and address. I am also open to adding a spot for a qr code linked to the stylist instagram or the salon booking link.

primary brand colors:
#333333 #233415 #36502a #93874a #000000
Mission statement:
Vessolin Hair Studio, a high-end salon located in the lively Downtown Farmington, Michigan, is committed to providing exceptional services in a welcoming and relaxed environment to meet the needs of our diverse clientele.
Our salon specializes in contemporary custom haircuts, coloring, extensions, and barbering and beard grooming services. Our team of skilled stylists is passionate and inventive in their hair styling techniques. At the heart of our salon are values centered on quality, innovation, creativity, and above all, comfort. These core values are evident in every appointment across our customizable array of services.
Our goal is to establish a benchmark for exceptional hair care for every human.
Website: www.vessolinhairstudio.example
instagram: @vessolinhairstudio
address: 41782 Pelham Crest Rd, Farmington MI
phone: 248-613-4087

Industry/Entity Type

Hair Salon

Contact Information for Business Card

Stylist name, title, phone, instagram, website, address, (optional qr code)

Requirements
Should not have
• Does not need mission statement on the card.

```html
<!DOCTYPE html>
<html lang="en">
<head>
<meta charset="utf-8">
<title>Vessolin Hair Studio – Business Card</title>
<link href="https://fonts.googleapis.com/css2?family=Oswald:wght@300&family=Poppins:wght@400;600&display=swap" rel="stylesheet">
<style>
  :root {
    --stage: #333333;
    --gold: #93874a;
    --gold-soft: #8c8046;
    --ink: #111111;
    --paper: #ffffff;
  }
  * { box-sizing: border-box; margin: 0; padding: 0; }
  html, body { width: 1200px; height: 1079px; overflow: hidden; background: var(--stage); }
  .stage { position: relative; width: 1200px; height: 1079px; }
  .card {
    position: absolute; top: 111px; width: 487px; height: 851px;
    background: var(--gold);
    box-shadow: 0 12px 30px rgba(0,0,0,0.45);
    overflow: hidden;
  }
  .card--front { left: 88px; }
  .card--back { left: 626px; }
  .pattern-field {
    position: absolute; inset: 0;
    background: linear-gradient(160deg, var(--gold-soft), var(--gold) 60%);
  }
  .brand-mark {
    position: absolute; display: flex; align-items: center; justify-content: center;
    border: 3px solid var(--paper); border-radius: 50%;
    color: var(--paper); font-family: "Poppins", sans-serif; font-weight: 600;
    text-align: center; text-transform: uppercase; letter-spacing: 0.12em; line-height: 1.35;
  }
  .card--front .brand-mark { left: 95px; top: 264px; width: 282px; height: 282px; font-size: 24px; }
  .card--back .brand-mark { left: 137px; top: 87px; width: 204px; height: 204px; font-size: 18px; }

  .web-band {
    position: absolute; left: 45px; right: 0; top: 650px; height: 73px;
    background: var(--paper); display: flex; align-items: center; padding-left: 26px;
    font-family: "Poppins", sans-serif; font-size: 22px; color: var(--ink);
  }
  .web-band strong { font-weight: 600; }
  .web-band::before {
    content: ""; position: absolute; left: -3px; top: 4px; width: 7px; height: 65px; background: var(--ink);
  }

  .info-panel {
    position: absolute; left: 61px; right: 0; top: 346px; height: 441px; background: var(--paper);
  }
  .info-bar { position: absolute; left: 56px; top: 382px; width: 10px; height: 378px; background: var(--ink); }
  .stylist-name {
    position: absolute; left: 55px; top: 78px;
    font-family: "Oswald", sans-serif; font-weight: 300; font-size: 50px; letter-spacing: 0.02em;
    color: var(--ink); line-height: 1; text-transform: uppercase;
  }
  .studio-name {
    position: absolute; left: 55px; top: 132px;
    font-family: "Poppins", sans-serif; font-size: 15px; color: var(--gold); text-transform: uppercase;
  }
  .contact-list { position: absolute; left: 55px; top: 182px; list-style: none; }
  .contact-item {
    display: flex; align-items: flex-start; gap: 16px;
    font-family: "Poppins", sans-serif; font-size: 19.5px; color: var(--ink); line-height: 1.35;
  }
  .contact-item + .contact-item { margin-top: 14px; }
  .contact-item svg { flex: none; width: 24px; height: 24px; margin-top: 2px; }
</style>
</head>
<body>
<main class="stage">
  <section class="card card--front">
    <div class="pattern-field" role="img" aria-label="Faint repeating brand pattern"></div>
    <div class="brand-mark">Vessolin<br>Hair Studio</div>
    <p class="web-band">www.<strong>vessolinhairstudio</strong>.example</p>
  </section>

  <section class="card card--back">
    <div class="pattern-field" role="img" aria-label="Faint repeating brand pattern"></div>
    <div class="brand-mark">Vessolin<br>Hair Studio</div>
    <div class="info-panel">
      <h1 class="stylist-name">Marcus Delane</h1>
      <p class="studio-name">Vessolin Hair Studio</p>
      <ul class="contact-list">
        <li class="contact-item">
          <svg viewBox="0 0 24 24" aria-hidden="true"><path d="M12 2a7 7 0 0 0-7 7c0 5 7 13 7 13s7-8 7-13a7 7 0 0 0-7-7zm0 9.5A2.5 2.5 0 1 1 12 6.5a2.5 2.5 0 0 1 0 5z" fill="#93874a"/></svg>
          <span>41782 Pelham Crest Rd,<br>Farmington MI</span>
        </li>
        <li class="contact-item">
          <svg viewBox="0 0 24 24" aria-hidden="true"><path d="M6.6 10.8a15 15 0 0 0 6.6 6.6l2.2-2.2c.3-.3.7-.4 1-.2 1.1.4 2.3.6 3.6.6.6 0 1 .4 1 1V20c0 .6-.4 1-1 1A17 17 0 0 1 3 4c0-.6.4-1 1-1h3.5c.6 0 1 .4 1 1 0 1.3.2 2.5.6 3.6.1.3 0 .7-.2 1z" fill="#93874a"/></svg>
          <span>248-613-4087</span>
        </li>
        <li class="contact-item">
          <svg viewBox="0 0 24 24" aria-hidden="true"><g fill="none" stroke="#93874a" stroke-width="2"><circle cx="12" cy="12" r="9.5"/><ellipse cx="12" cy="12" rx="4" ry="9.5"/><path d="M2.5 12h19M4 7h16M4 17h16"/></g></svg>
          <span>www.vessolinhairstudio.example</span>
        </li>
        <li class="contact-item">
          <svg viewBox="0 0 24 24" aria-hidden="true"><circle cx="12" cy="12" r="10" fill="#93874a"/></svg>
          <span>@vessolinhairstudio</span>
        </li>
      </ul>
    </div>
    <div class="info-bar"></div>
  </section>
</main>
</body>
</html>
```